Workshop PPT Update for AI Transformation Sessions

Our strategic consulting firm runs strategy workshops using slides as workshop exercises. These slides are used to communicate to the participants in advance, run the workshops and produce the final deliverable.

It is time for a design "upgrade". We'd like them to be more engaging, hipper and more interesting. These slides are utilitarian, so clean and usable is good. I have attached the example of what we have today. I have also attached an example of another company's slides that I like.

We can't rip off their design nor can we go away 100% from what we have. But I think it is possible to "update" our look to something closer to their look. Grey colors are fine with some color pop.

Slide styles needed are - 1) Cover Page, 2) Instructions Page, 3) Bullet list 4) Worksheet (place for participants to add content 5) Table, 6) Two column.

```html
<!DOCTYPE html>
<html lang="en">
<head>
<meta charset="utf-8">
<title>AI Transformation Workshop Slides</title>
<link href="https://fonts.googleapis.com/css2?family=Poppins:wght@400;500;600&family=Raleway:wght@300;400;500;600&display=swap" rel="stylesheet">
<style>
  :root{
    --red:#b03a37;
    --red-deep:#9c302d;
    --ink:#3f4250;
    --ink-2:#4a4d5c;
    --text:#2b2d36;
    --muted:#5d606c;
    --paper:#f5f6f8;
    --row:#e8eaee;
    --frame:#55575f;
    --white:#ffffff;
  }
  *{box-sizing:border-box;margin:0;padding:0}
  html,body{width:1200px;height:4030px;overflow:hidden}
  body{background:var(--frame);font-family:"Raleway",sans-serif;color:var(--text);position:relative}
  .slide{position:absolute;left:12px;width:1176px;height:664px;overflow:hidden;
    background:radial-gradient(circle at 95% 8%,#e3e5ea 0,rgba(245,246,248,0) 38%),
               radial-gradient(circle at 4% 92%,#e6e8ec 0,rgba(245,246,248,0) 35%),var(--paper)}
  .s1{top:12px}.s2{top:682px}.s3{top:1352px}.s4{top:2022px}.s5{top:2692px}.s6{top:3362px}
  .abs{position:absolute}
  .footer{position:absolute;left:0;bottom:0;width:100%;height:47px;background:var(--ink);
    color:var(--white);font-family:"Raleway",sans-serif;font-weight:600;font-size:11px}
  .footer .copy{position:absolute;left:71px;top:17px}
  .footer .page{position:absolute;left:1044px;top:17px;font-size:12px}
  .brand{position:absolute;left:830px;top:-6px;width:143px;height:50px;background:var(--white);
    display:flex;align-items:center;justify-content:center;gap:6px;
    font-family:"Poppins",sans-serif;font-weight:500;font-size:21px;color:var(--ink)}
  .brand i{display:block;width:9px;height:9px;border-radius:50%;background:var(--red)}
  .title{font-family:"Poppins",sans-serif;font-weight:500;color:var(--red);font-size:40px;line-height:1.1}
  .center{left:0;width:100%;text-align:center}
  /* slide 1 */
  .start-list{left:650px;top:185px;width:470px;list-style:none}
  .start-list li{font-weight:300;font-size:27px;line-height:1.15;margin-bottom:28px;position:relative;padding-left:0}
  .start-list svg{width:22px;height:22px;vertical-align:-2px;margin-right:6px}
  /* slide 2 */
  .subtitle{font-family:"Raleway",sans-serif;font-weight:600;font-size:26px;color:var(--muted)}
  /* boxes */
  .dark-box{background:var(--ink-2);border-radius:10px;color:var(--white);font-family:"Poppins",sans-serif}
  .overview{left:78px;top:168px;width:374px;height:374px;padding:22px 33px}
  .overview p{font-weight:500;font-size:21px;line-height:49px}
  .divider{left:587px;top:24px;width:2px;height:572px;background:#9a9ca5}
  .flow{left:655px;top:0;width:500px}
  .flow-item{position:absolute;left:0;width:500px;height:50px}
  .flow-item .num{position:absolute;left:0;top:-20px;font-family:"Poppins",sans-serif;font-weight:600;font-size:28px;color:#c4c6cc}
  .flow-item .ico{position:absolute;left:28px;top:0;width:48px;height:48px;border-radius:50%;background:var(--red);
    box-shadow:0 0 0 3px #f0d3d2}
  .flow-item .txt{position:absolute;left:92px;top:6px;width:330px}
  .flow-item b{display:block;font-family:"Poppins",sans-serif;font-weight:500;font-size:14px;color:var(--text)}
  .flow-item small{display:block;font-size:10px;line-height:1.3;color:var(--text);margin-top:2px}
  .deliv{left:696px;top:530px;font-family:"Poppins",sans-serif;font-size:15px;line-height:21px;color:var(--text)}
  /* slide 4 */
  .materials{left:78px;top:168px;width:374px;height:374px;padding:18px 33px}
  .materials p{font-weight:500;font-size:17px;line-height:35px}
  .materials p.two{line-height:22px;padding:7px 0 6px}
  .instructions{left:504px;top:120px;width:620px;font-family:"Poppins",sans-serif;font-weight:500;color:#111}
  .instructions .purpose{font-size:25px;line-height:33px;margin-bottom:10px}
  .instructions p{font-size:19px;line-height:26px;margin-bottom:16px}
  /* slide 5 */
  .principle{position:absolute;top:240px;width:196px;text-align:center}
  .badge{width:110px;height:110px;border-radius:50%;margin:0 auto;background:radial-gradient(circle at 40% 35%,#c3463f,var(--red-deep));
    border:4px solid #e9d9d8;box-shadow:0 4px 8px rgba(0,0,0,.25);color:var(--white);
    font-family:"Poppins",sans-serif;font-weight:600;font-size:48px;line-height:102px}
  .principle h3{font-family:"Poppins",sans-serif;font-weight:500;font-size:19px;color:var(--muted);margin-top:18px}
  .principle p{font-size:12.5px;line-height:17px;color:var(--muted);margin-top:4px}
  /* slide 6 */
  .plan{position:absolute;left:77px;top:182px;width:1041px;border-collapse:separate;border-spacing:4px 4px;
    font-family:"Poppins",sans-serif;font-size:15px;color:var(--text);text-align:center}
  .plan th{background:var(--ink);color:var(--white);font-weight:600;font-size:15px;height:38px}
  .plan td{background:var(--row);height:60px;line-height:1.3}
</style>
</head>
<body>

<!-- Slide 1: Getting Started -->
<section class="slide s1">
  <svg class="abs" style="left:0;top:0" width="640" height="617" viewBox="0 0 640 617">
    <defs>
      <linearGradient id="photoTone" x1="0" y1="0" x2="1" y2="1">
        <stop offset="0" stop-color="#7b7f86"/>
        <stop offset=".5" stop-color="#3c4653"/>
        <stop offset="1" stop-color="#151a22"/>
      </linearGradient>
    </defs>
    <path d="M0 0 H478 Q640 290 560 617 H0 Z" fill="var(--red)"/>
    <path d="M0 0 H450 Q608 290 530 617 H0 Z" fill="var(--white)"/>
    <path d="M0 0 H440 Q596 290 518 617 H0 Z" fill="url(#photoTone)" role="img" aria-label="Photo of two colleagues smiling at a laptop in an office"/>
  </svg>
  <h1 class="title abs" style="left:650px;top:90px">Getting Started</h1>
  <ul class="start-list abs">
    <li><svg viewBox="0 0 22 22"><circle cx="11" cy="11" r="10" fill="var(--ink)"/><path d="M6 11h8M11 7l4 4-4 4" stroke="#fff" stroke-width="2.4" fill="none"/></svg>Complete the Engagement Sizing Survey.</li>
    <li><svg viewBox="0 0 22 22"><circle cx="11" cy="11" r="10" fill="var(--ink)"/><path d="M6 11h8M11 7l4 4-4 4" stroke="#fff" stroke-width="2.4" fill="none"/></svg>Collect relevant inputs.</li>
    <li><svg viewBox="0 0 22 22"><circle cx="11" cy="11" r="10" fill="var(--ink)"/><path d="M6 11h8M11 7l4 4-4 4" stroke="#fff" stroke-width="2.4" fill="none"/></svg>Determine workshop participants &amp; date.</li>
    <li><svg viewBox="0 0 22 22"><circle cx="11" cy="11" r="10" fill="var(--ink)"/><path d="M6 11h8M11 7l4 4-4 4" stroke="#fff" stroke-width="2.4" fill="none"/></svg>Send invites, to include pre-work.</li>
  </ul>
  <footer class="footer"><span class="copy">©Copyrights 2023 NorthPath |All Rights Reserved</span><span class="brand"><i></i>NorthPath</span><span class="page">Page |01</span></footer>
</section>

<!-- Slide 2: Cover -->
<section class="slide s2">
  <div class="abs" style="left:791px;top:0;width:385px;height:617px;background:var(--red)"></div>
  <div class="abs" role="img" aria-label="Photo of a businesswoman wearing a glowing tech headset holding a tablet" style="left:625px;top:66px;width:471px;height:487px;background:linear-gradient(135deg,#2b3a4e,#6a4a3a 55%,#1a1f2a)"></div>
  <h1 class="title abs" style="left:71px;top:218px">Kickoff &amp; Discovery</h1>
  <p class="subtitle abs" style="left:71px;top:300px">Sizing &amp; Scoping AI Transformation</p>
  <footer class="footer"><span class="copy">©Copyrights 2023 NorthPath |All Rights Reserved</span><span class="brand"><i></i>NorthPath</span><span class="page">Page |02</span></footer>
</section>

<!-- Slide 3: Two column -->
<section class="slide s3">
  <h2 class="title abs" style="left:71px;top:40px">Workshop Overview</h2>
  <div class="dark-box overview abs">
    <p>Participants: Execs</p><p>Duration: 2 hrs.</p><p>Prep Work:</p><p>Org Strategy</p><p>2023 Goal Performance</p><p>Existing policies</p><p>Pre-thinking questions</p>
  </div>
  <div class="divider abs"></div>
  <h2 class="title abs" style="left:660px;top:40px">Workshop Flow</h2>
  <div class="flow abs">
    <div class="flow-item" style="top:119px"><span class="num">01</span><span class="ico"></span><div class="txt"><b>Confirm Company Direction</b><small>Recap organizational purpose, values, vision &amp; winning strategy.</small></div></div>
    <div class="flow-item" style="top:185px"><span class="num">02</span><span class="ico"></span><div class="txt" style="top:14px"><b>Develop AI Vision</b></div></div>
    <div class="flow-item" style="top:251px"><span class="num">03</span><span class="ico"></span><div class="txt"><b>Develop AI Guiding Principles</b><small>Developed AI Guiding Principles, supporting policies to include approved tools.</small></div></div>
    <div class="flow-item" style="top:318px"><span class="num">04</span><span class="ico"></span><div class="txt"><b>Agree on a Governance Approach</b><small>Agreed upon governance approach, structure, &amp; executive champion.</small></div></div>
    <div class="flow-item" style="top:389px"><span class="num">05</span><span class="ico"></span><div class="txt"><b>Agree on a Training &amp; Learning Approach</b><small>Set approach to training &amp; continuous learning.</small></div></div>
    <div class="flow-item" style="top:463px"><span class="num">06</span><span class="ico"></span><div class="txt"><b>Determine Rollout &amp; Communication</b><small>Organizational rollout &amp; continuous communication.</small></div></div>
  </div>
  <p class="deliv abs">Deliverables<br>Your Company's AI Playbook</p>
  <footer class="footer"><span class="copy">©Copyrights 2023 NorthPath |All Rights Reserved</span><span class="brand"><i></i>NorthPath</span><span class="page">Page |03</span></footer>
</section>

<!-- Slide 4: Instructions -->
<section class="slide s4">
  <h2 class="title abs center" style="top:40px">Creating your AI Guiding Principles</h2>
  <div class="dark-box materials abs">
    <p>Your Existing Material</p><p>Company Values</p><p class="two">Current Policies (GDPR, CCPA, etc.)</p><p>Legal Guidance</p><p>OTHER</p><p>Examples for Inspiration</p><p>See next slides</p><p>ChatBot Prompts</p><p>HERE</p>
  </div>
  <div class="instructions abs">
    <p class="purpose">Purpose: To create behavioral statements that everyone is expected to adhere to.</p>
    <p>Instructions:</p>
    <p>Create the Outline.<br>Determine the topics that need a principle.</p>
    <p>Audit the Outline.<br>Look at the current policies to determine if all topics are covered.</p>
    <p>Draft the Guiding Principles.</p>
    <p>Determine which GPs need detailed policies.</p>
    <p>Determine which AI Tools support the GPs.</p>
    <p>Finalize via a legal and executive review.</p>
  </div>
  <footer class="footer"><span class="copy">©Copyrights 2023 NorthPath |All Rights Reserved</span><span class="brand"><i></i>NorthPath</span><span class="page">Page |04</span></footer>
</section>

<!-- Slide 5: Worksheet -->
<section class="slide s5">
  <h2 class="title abs center" style="top:103px">AI Guiding Principles</h2>
  <p class="abs center" style="top:164px;font-family:'Poppins',sans-serif;font-size:22px;color:var(--ink)">What guides our decision-making and approach?</p>
  <div class="principle" style="left:64px"><div class="badge">01</div><h3>Principle #1</h3><p>Complete perspective from Executives, Directors, Managers &amp; Staff. Conduct competitive analysis and customer research (optional).</p></div>
  <div class="principle" style="left:282px"><div class="badge">02</div><h3>Principle #2</h3><p>Complete perspective from Executives, Directors, Managers &amp; Staff. Conduct competitive analysis and customer research (optional).</p></div>
  <div class="principle" style="left:499px"><div class="badge">03</div><h3>Principle #3</h3><p>Complete perspective from Executives, Directors, Managers &amp; Staff. Conduct competitive analysis and customer research (optional).</p></div>
  <div class="principle" style="left:715px"><div class="badge">04</div><h3>Principle #4</h3><p>Complete perspective from Executives, Directors, Managers &amp; Staff. Conduct competitive analysis and customer research (optional).</p></div>
  <div class="principle" style="left:933px"><div class="badge">05</div><h3>Principle #5</h3><p>Complete perspective from Executives, Directors, Managers &amp; Staff. Conduct competitive analysis and customer research (optional).</p></div>
  <footer class="footer"><span class="copy">©Copyrights 2023 NorthPath |All Rights Reserved</span><span class="brand"><i></i>NorthPath</span><span class="page">Page |05</span></footer>
</section>

<!-- Slide 6: Table -->
<section class="slide s6">
  <h2 class="title abs center" style="top:80px">Plan Structure</h2>
  <table class="plan">
    <colgroup><col style="width:122px"><col style="width:146px"><col style="width:295px"><col style="width:218px"><col style="width:244px"></colgroup>
    <thead><tr><th colspan="2">Level</th><th>Planning Element &amp; Definition</th><th>Accountability/Owner</th><th>Frequency of Modification</th></tr></thead>
    <tbody>
      <tr><td style="height:52px">1</td><td>What (overall)</td><td>Strategic Priorities</td><td>N/A</td><td>3+ years</td></tr>
      <tr><td style="height:68px">1.1</td><td>What<br>(this year)</td><td>Goals (Outcomes &amp; Strategies )</td><td>Executive Leadership</td><td>1-3 years</td></tr>
      <tr><td style="height:68px">1.1.1</td><td>How</td><td>Key Performance Indicators<br>and/or Initiatives</td><td>Executive Leadership</td><td style="font-size:13px">1 year<br>(w/ qrtly targets)</td></tr>
      <tr><td style="height:64px">1.1.1</td><td>How</td><td>Action Items</td><td></td><td>Quarterly/Monthly</td></tr>
    </tbody>
  </table>
  <footer class="footer"><span class="copy">©Copyrights 2023 NorthPath |All Rights Reserved</span><span class="brand"><i></i>NorthPath</span><span class="page">Page |06</span></footer>
</section>

</body>
</html>
```